Meridale Nutrition needs Stationary and a business card

We would like to use our current logo. The text can be moved around as needed. The stationary needs to be a 'first page' where the logo is more prominent to be impressive on higher quality paper and a second page where the logo is more subtle where there will be much more information on the page. There are 2 clinic locations which will need include name, address, phone number, fax number, web address. The business card should be single sided and contain this information also.
The design must be contemporary and sophisticated as this is a science based diet run out of a medical clinic.

Target Market(s)

People wanting to lose weight, athletes looking to optimise performance, people with arthritis or fighting cancer

Industry/Entity Type

Business

Contact Information for Business Card

must use the logo. I have attached an example card with the practice details on it. there must be space for the doctors name. Also the website www.meridalenutrition.com.au

Requirements
Must have
• the logo, the business adresses and phone numbers, the website, the doctors name and qualifications
Nice to have
• some creativity
Should not have
• Do not simply reproduce the existing card please

```html
<!DOCTYPE html>
<html lang="en">
<head>
<meta charset="utf-8">
<title>Meridale Nutrition – Business Card</title>
<link rel="stylesheet" href="https://fonts.googleapis.com/css2?family=Open+Sans:wght@400;600;700&family=PT+Sans+Narrow&display=swap">
<style>
  :root {
    --backdrop: #2f2f2f;
    --card: #fafafa;
    --navy: #2c5d9a;
    --cyan: #1cb8f0;
    --ink: #444444;
    --white: #ffffff;
  }
  * { margin: 0; padding: 0; box-sizing: border-box; }
  html, body {
    width: 1200px; height: 750px; overflow: hidden;
    background: var(--backdrop);
  }
  .business-card {
    position: absolute; left: 50px; top: 61px;
    width: 1100px; height: 628px;
    background: var(--card);
    font-family: "Open Sans", sans-serif;
    overflow: hidden;
  }
  .location {
    position: absolute; left: 69px;
    font-size: 28px; line-height: 39px; color: var(--ink);
  }
  .location h2, .location .label {
    font-size: 30px; font-weight: 600; color: var(--navy);
  }
  .location h2 { font-weight: 600; }
  .location--westmere { top: 66px; }
  .location--kellford { top: 234px; }
  .location--shoulder { top: 404px; }
  .location--knee { top: 488px; }
  .brand-mark {
    position: absolute; left: 700px; top: 82px;
    width: 236px; height: 236px;
  }
  .brand-name {
    position: absolute; left: 569px; top: 338px; width: 498px;
    text-align: center;
    font-size: 34px; font-weight: 700; letter-spacing: 0.5px;
    color: var(--navy); text-transform: uppercase;
  }
  .doctor-band {
    position: absolute; left: 569px; top: 428px;
    width: 531px; height: 135px;
    background: var(--navy);
    text-align: right; padding: 0 85px 0 0;
  }
  .doctor-name {
    font-size: 40px; font-weight: 600; color: var(--cyan);
    line-height: 50px; padding-top: 1px;
  }
  .doctor-credentials {
    font-family: "PT Sans Narrow", sans-serif;
    font-size: 27px; line-height: 41px; color: var(--white);
  }
</style>
</head>
<body>
  <div class="business-card">
    <div class="location location--westmere">
      <h2>Westmere</h2>
      <p>52-54 Harrow Street</p>
      <p>Westmere NSW 2139</p>
      <p><span class="label">Tel:</span> 02 5550 1842</p>
    </div>
    <div class="location location--kellford">
      <h2>Kellford</h2>
      <p>118 Tamsin Road</p>
      <p>Kellford NSW 2034</p>
      <p><span class="label">Tel:</span> 02 5550 7316</p>
    </div>
    <div class="location location--shoulder">
      <h2>Shoulder and Elbow</h2>
      <p>www.drvarn.com.au</p>
    </div>
    <div class="location location--knee">
      <h2>Knee surgery</h2>
      <p>www.varnknee.com.au</p>
    </div>

    <svg class="brand-mark" viewBox="0 0 236 236" aria-hidden="true">
      <circle cx="118" cy="118" r="118" fill="var(--cyan)"/>
    </svg>
    <div class="brand-name">Meridale Nutrition</div>

    <div class="doctor-band">
      <p class="doctor-name">Dr Elias Varn</p>
      <p class="doctor-credentials">MBBS (NSW) MBiomedE FRACS (Ortho)</p>
      <p class="doctor-credentials">FAOrthA Orthopaedic Surgeon</p>
    </div>
  </div>
</body>
</html>
```